Vantor Wear and Fuel is looking for a Clothing/Supplement Online Store Website!

Must be convenient, and user friendly, with vibrant colors that catch the eye!

Target Market(s)

Athletes, and Fashion Customers

Industry/Entity Type

Fitness

Coding

Coded - Design and coding required

Number of Pages Required

3 page

Font styles to use
Decorative

Colors

Designer to choose colors to be used in the design.

Requirements
Must have
• Somewhere to feature products, features to promote discounts and make announcements.
Nice to have
• My logos on each page

```html
<!DOCTYPE html>
<html lang="en">
<head>
<meta charset="utf-8">
<title>Vantor Wear and Fuel — Store</title>
<link rel="stylesheet" href="https://fonts.googleapis.com/css2?family=Montserrat:wght@400;500;600;700;800;900&display=swap">
<style>
:root{
  --cyan:#1ec8f0;
  --cyan-dark:#0fa9d1;
  --ink:#111315;
  --black:#000;
  --white:#fff;
  --grey:#6f7377;
  --line:#d9dcdf;
  --tile:#2a2d31;
  --star:#222;
}
*{box-sizing:border-box;margin:0;padding:0}
html,body{width:1200px;height:4008px;overflow:hidden;background:var(--white)}
body{font-family:"Montserrat",Arial,sans-serif;color:var(--ink);position:relative}
.btn{display:inline-block;background:var(--cyan);color:var(--white);font-weight:700;font-size:15px;letter-spacing:.5px;border-radius:22px;padding:12px 26px;text-transform:uppercase}

/* promo bar */
.promo{height:72px;background:var(--black);color:var(--white);display:flex;align-items:center;justify-content:center;font-weight:800;font-size:30px;letter-spacing:.5px;gap:10px}
.promo em{font-style:normal;color:var(--cyan)}
.promo small{font-size:18px;font-weight:700}

/* header */
.site-header{height:80px;display:flex;align-items:center;padding:0 110px;border-bottom:1px solid var(--line)}
.brand{font-weight:900;font-size:40px;letter-spacing:1px;color:var(--ink);display:flex;align-items:center;gap:10px}
.brand-dot{width:14px;height:14px;background:var(--cyan);border-radius:50%}
.main-nav{margin-left:auto;display:flex;gap:30px;font-weight:700;font-size:15px}
.main-nav .active{color:var(--cyan)}
.header-tools{display:flex;gap:12px;align-items:center;margin-left:40px}
.tool{width:30px;height:30px;border-radius:50%;background:var(--cyan);display:flex;align-items:center;justify-content:center}
.search{width:200px;height:32px;border:1px solid var(--line);border-radius:16px;display:flex;align-items:center;justify-content:space-between;padding:0 12px;font-size:13px;color:var(--grey)}

/* hero */
.hero{position:relative;height:440px;background:linear-gradient(90deg,#1b1d20 0%,#4a4e54 45%,#767b80 70%,#3a3d41 100%)}
.hero-copy{position:absolute;left:110px;top:120px;color:var(--white)}
.hero-title{font-weight:800;font-size:64px;letter-spacing:2px}
.hero-text{font-size:17px;font-weight:600;line-height:1.4;width:330px;margin:10px 0 22px}
.hero-pill{position:absolute;right:40px;top:272px;background:var(--cyan);color:var(--white);font-weight:700;font-size:13px;border-radius:16px;padding:7px 16px}

/* perks */
.perks{position:absolute;top:614px;left:0;width:1200px;display:flex;justify-content:center;gap:92px}
.perk{width:180px;text-align:center}
.perk-circle{width:180px;height:180px;border-radius:50%;background:var(--white);border:4px solid var(--cyan);display:flex;flex-direction:column;align-items:center;justify-content:center;gap:10px;box-shadow:0 4px 14px rgba(0,0,0,.12)}
.perk-label{font-weight:700;font-size:13px;width:130px;line-height:1.25}

/* categories */
.categories{position:absolute;top:888px;left:112px;width:976px;display:flex;gap:16px}
.category{flex:1;height:184px;background:linear-gradient(160deg,#3b3f44,#16181a);display:flex;flex-direction:column;align-items:center;justify-content:center;gap:14px;color:var(--white)}
.category-name{font-weight:800;font-size:20px;letter-spacing:.5px}
.category .btn-outline{border:2px solid var(--white);border-radius:18px;padding:7px 20px;font-weight:700;font-size:13px}

/* section titles */
.section-title{position:absolute;left:0;width:1200px;text-align:center;font-weight:900;font-size:38px;letter-spacing:1px}

/* best sellers */
.best-grid{position:absolute;top:1220px;left:0;width:1200px;display:grid;grid-template-columns:repeat(5,1fr);grid-template-rows:222px 222px;gap:4px}
.best-grid div{background:linear-gradient(150deg,#4b4f55,#1d1f22)}
.best-grid div:nth-child(3n){background:linear-gradient(150deg,#8a8f95,#3a3d41)}
.best-grid div:nth-child(4n){background:linear-gradient(150deg,#2f6f8f,#15181b)}

/* feature products */
.tabs{position:absolute;top:1826px;left:0;width:1200px;display:flex;justify-content:center;gap:14px}
.tab{border:2px solid var(--ink);font-weight:700;font-size:12px;padding:8px 14px;letter-spacing:.3px}
.products{position:absolute;top:1900px;left:148px;width:904px;display:grid;grid-template-columns:repeat(4,200px);column-gap:34px;row-gap:36px}
.product{text-align:center}
.product-card{height:300px;border:1px solid var(--line);display:flex;flex-direction:column;align-items:center;padding:16px 10px 0}
.product-shot{width:150px;height:170px}
.product-name{font-weight:800;font-size:15px;margin-top:14px}
.stars{font-size:15px;color:var(--star);letter-spacing:2px;margin-top:4px}
.price{font-weight:800;font-size:18px;margin-top:4px}
.product .btn{margin-top:14px;font-size:13px;padding:9px 20px}

/* gym band */
.gym-band{position:absolute;top:2708px;left:0;width:1200px;height:492px;background:linear-gradient(100deg,#6b6258 0%,#2c2a28 45%,#3d4856 70%,#1a1c1f 100%)}

/* newsletter */
.newsletter{position:absolute;top:3200px;left:0;width:1200px;height:540px;background:linear-gradient(180deg,#000 0%,#0b0c0d 60%,#000 100%);color:var(--white);text-align:center;padding-top:40px}
.newsletter h2{font-weight:900;font-size:40px;letter-spacing:1px}
.newsletter p{font-size:17px;font-weight:600;margin:12px 0 24px}
.showcase{position:absolute;left:200px;top:210px;width:800px;height:330px;background:radial-gradient(ellipse at 60% 45%,#3b4653 0%,#1a1d21 55%,#000 100%)}

/* footer */
.site-footer{position:absolute;top:3740px;left:0;width:1200px;height:268px;background:var(--black);color:var(--white)}
.footer-inner{display:flex;padding:24px 110px 0;gap:56px}
.footer-brand{font-weight:900;font-size:46px;letter-spacing:1px;display:flex;align-items:center;gap:10px;width:250px;margin-top:16px}
.footer-col h4{font-weight:800;font-size:15px;margin-bottom:8px}
.footer-col li{list-style:none;font-size:14px;line-height:1.5;color:#d3d6d9}
.socials{display:flex;gap:10px;margin-bottom:14px}
.socials span{width:34px;height:34px;border:2px solid var(--white);border-radius:50%}
.cards{display:flex;gap:6px}
.cards span{width:36px;height:24px;background:#e6e8ea;border-radius:3px}
.cards span:nth-child(2){background:#f29a2e}
.cards span:nth-child(3){background:#2f7fd0}
.cards span:nth-child(4){background:#c9d2dc}
.copyright{position:absolute;bottom:18px;left:0;width:1200px;text-align:center;font-size:13px;color:#bfc3c7}
</style>
</head>
<body>

<div class="promo">SUBSCRIBE &amp; SAVE <small>up to</small> <em>15% OFF</em> <small>plus</small> <em>FREE SHIPPING</em></div>

<header class="site-header">
  <div class="brand">VANTOR<span class="brand-dot"></span></div>
  <nav class="main-nav">
    <span class="active">SHOP</span><span>SUPPLEMENTS</span><span>APPAREL</span>
  </nav>
  <div class="header-tools">
    <span class="tool"><svg width="14" height="14" viewBox="0 0 14 14"><circle cx="7" cy="4.5" r="3" fill="#fff"/><path d="M1 14c0-4 3-6 6-6s6 2 6 6z" fill="#fff"/></svg></span>
    <span class="tool"><svg width="14" height="14" viewBox="0 0 14 14"><path d="M1 2h2l2 8h7l1.5-6H4" fill="none" stroke="#fff" stroke-width="1.6"/><circle cx="6" cy="12.5" r="1.2" fill="#fff"/><circle cx="11" cy="12.5" r="1.2" fill="#fff"/></svg></span>
    <div class="search">Search<svg width="14" height="14" viewBox="0 0 14 14"><circle cx="6" cy="6" r="4.5" fill="none" stroke="#1ec8f0" stroke-width="2"/><path d="M9.5 9.5 13 13" stroke="#1ec8f0" stroke-width="2"/></svg></div>
  </div>
</header>

<section class="hero" role="img" aria-label="Athlete in a grey hoodie drinking from a shaker bottle in a gym">
  <div class="hero-copy">
    <h1 class="hero-title">VANTOR</h1>
    <p class="hero-text">Train harder, recover faster and wear gear built for every rep you take.</p>
    <span class="btn">Shop Now</span>
  </div>
  <span class="hero-pill">Join Rewards</span>
</section>

<div class="perks">
  <div class="perk"><div class="perk-circle">
    <svg width="64" height="44" viewBox="0 0 64 44"><rect x="2" y="6" width="36" height="26" fill="none" stroke="#111" stroke-width="3"/><path d="M38 14h14l9 10v8H38z" fill="none" stroke="#111" stroke-width="3"/><circle cx="14" cy="36" r="5" fill="#fff" stroke="#111" stroke-width="3"/><circle cx="50" cy="36" r="5" fill="#fff" stroke="#111" stroke-width="3"/></svg>
    <span class="perk-label">FREE DELIVERY</span></div></div>
  <div class="perk"><div class="perk-circle">
    <svg width="50" height="50" viewBox="0 0 50 50"><circle cx="25" cy="20" r="14" fill="none" stroke="#111" stroke-width="3"/><path d="M18 20l5 5 9-10" fill="none" stroke="#1ec8f0" stroke-width="3"/><path d="M15 31l-5 15 9-4 4 6 2-14M35 31l5 15-9-4-4 6" fill="none" stroke="#111" stroke-width="3"/></svg>
    <span class="perk-label">QUALITY PRODUCTS</span></div></div>
  <div class="perk"><div class="perk-circle">
    <svg width="50" height="50" viewBox="0 0 50 50"><circle cx="25" cy="25" r="20" fill="none" stroke="#111" stroke-width="3"/><path d="M31 17c-2-2-12-3-12 3s12 3 12 10-10 5-13 2M25 11v28" fill="none" stroke="#111" stroke-width="3"/></svg>
    <span class="perk-label">MONEY-BACK GUARANTEE</span></div></div>
  <div class="perk"><div class="perk-circle">
    <svg width="50" height="50" viewBox="0 0 50 50"><path d="M9 28v-5a16 16 0 0 1 32 0v5" fill="none" stroke="#111" stroke-width="3"/><rect x="5" y="26" width="8" height="13" rx="2" fill="#1ec8f0"/><rect x="37" y="26" width="8" height="13" rx="2" fill="#1ec8f0"/><path d="M41 39c0 5-6 7-12 7" fill="none" stroke="#111" stroke-width="3"/></svg>
    <span class="perk-label">ONLINE SUPPORT</span></div></div>
</div>

<div class="categories">
  <div class="category" role="img" aria-label="Supplement tubs on a dark background"><span class="category-name">SUPPLEMENTS</span><span class="btn-outline">VIEW SUPPLEMENTS</span></div>
  <div class="category" role="img" aria-label="Man in training apparel"><span class="category-name">MEN'S APPAREL</span><span class="btn-outline">VIEW APPAREL</span></div>
  <div class="category" role="img" aria-label="Woman in training apparel"><span class="category-name">WOMEN'S APPAREL</span><span class="btn-outline">VIEW APPAREL</span></div>
  <div class="category" role="img" aria-label="Gym equipment and gear"><span class="category-name">GEAR</span><span class="btn-outline">VIEW GEAR</span></div>
</div>

<h2 class="section-title" style="top:1146px">BEST SELLERS</h2>
<div class="best-grid" role="img" aria-label="Grid of ten photos of athletes wearing apparel and supplement products">
  <div></div><div></div><div></div><div></div><div></div>
  <div></div><div></div><div></div><div></div><div></div>
</div>

<h2 class="section-title" style="top:1738px">FEATURE PRODUCTS</h2>
<div class="tabs">
  <span class="tab">PEOPLE BUYING</span><span class="tab">NEW ARRIVALS</span><span class="tab">GIFTS UNDER $50</span><span class="tab">GIFTS OVER $100</span><span class="tab">GIFTS OVER $200</span>
</div>

<div class="products">
  <div class="product"><div class="product-card"><div class="product-shot" role="img" aria-label="Black supplement bottle" style="background:linear-gradient(90deg,#111,#3a3d41,#111)"></div><div class="product-name">SUPPLEMENT</div><div class="stars">★★★★★</div><div class="price">$230.00</div></div><span class="btn">Add to cart</span></div>
  <div class="product"><div class="product-card"><div class="product-shot" role="img" aria-label="Brown leather jacket" style="background:linear-gradient(90deg,#5a3220,#8b5536,#5a3220)"></div><div class="product-name">MEN'S APPAREL</div><div class="stars">★★★★★</div><div class="price">$23.50</div></div><span class="btn">Add to cart</span></div>
  <div class="product"><div class="product-card"><div class="product-shot" role="img" aria-label="Black bomber jacket" style="background:linear-gradient(90deg,#0e0f10,#2b2d30,#0e0f10)"></div><div class="product-name">MEN'S APPAREL</div><div class="stars">★★★★★</div><div class="price">$32.30</div></div><span class="btn">Add to cart</span></div>
  <div class="product"><div class="product-card"><div class="product-shot" role="img" aria-label="Lavender hoodie" style="background:linear-gradient(90deg,#7b78b8,#a3a0d8,#7b78b8)"></div><div class="product-name">WOMEN APPAREL</div><div class="stars">★★★★★</div><div class="price">$230.00</div></div><span class="btn">Add to cart</span></div>
  <div class="product"><div class="product-card"><div class="product-shot" role="img" aria-label="Black supplement tub" style="background:linear-gradient(90deg,#0c0d0e,#34373b,#0c0d0e)"></div><div class="product-name">SUPPLEMENT</div><div class="stars">★★★★★</div><div class="price">$230.00</div></div><span class="btn">Add to cart</span></div>
  <div class="product"><div class="product-card"><div class="product-shot" role="img" aria-label="White supplement tub" style="background:linear-gradient(90deg,#d8dadc,#f7f8f9,#d8dadc)"></div><div class="product-name">SUPPLEMENT</div><div class="stars">★★★★★</div><div class="price">$21.50</div></div><span class="btn">Add to cart</span></div>
  <div class="product"><div class="product-card"><div class="product-shot" role="img" aria-label="Black quilted jacket" style="background:linear-gradient(90deg,#0e0f10,#2e3034,#0e0f10)"></div><div class="product-name">WOMEN APPAREL</div><div class="stars">★★★★★</div><div class="price">$32.30</div></div><span class="btn">Add to cart</span></div>
  <div class="product"><div class="product-card"><div class="product-shot" role="img" aria-label="White supplement pouch" style="background:linear-gradient(90deg,#dcdee0,#f5f6f7,#dcdee0)"></div><div class="product-name">SUPPLEMENT</div><div class="stars">★★★★★</div><div class="price">$230.00</div></div><span class="btn">Add to cart</span></div>
</div>

<section class="gym-band" role="img" aria-label="Two athletes resting and talking in a gym"></section>

<section class="newsletter">
  <h2>GET THE LATEST INFO</h2>
  <p>On giveaways, nutritional advice, and much more. Become a Vantor insider.</p>
  <span class="btn">Sign Up Now</span>
  <div class="showcase" role="img" aria-label="Supplement tubs beside laptop, tablet and phone showing the store"></div>
</section>

<footer class="site-footer">
  <div class="footer-inner">
    <div class="footer-brand">VANTOR<span class="brand-dot"></span></div>
    <div class="footer-col"><h4>INFORMATION</h4><ul><li>Orders &amp; Deliveries</li><li>Privacy Policy</li><li>Terms &amp; Conditions</li><li>Site Map</li></ul></div>
    <div class="footer-col"><h4>CUSTOMER SERVICE</h4><ul><li>Gift Vouchers</li><li>About Us</li><li>Contact Us</li><li>Returns</li></ul></div>
    <div class="footer-col"><h4>MY ACCOUNT</h4><ul><li>My Account</li><li>Order History</li><li>Re-Order</li><li>Newsletter</li></ul></div>
    <div class="footer-col"><h4>CONNECT WITH US :</h4>
      <div class="socials"><span></span><span></span><span></span><span></span></div>
      <div class="cards"><span></span><span></span><span></span><span></span></div>
    </div>
  </div>
  <div class="copyright">Copyright © 2016 All Rights Reserved</div>
</footer>

</body>
</html>
```